Redesign of business card for Cedar Ridge Mechanical

We are looking for a new design for our business cards for Cedar Ridge Mechanical. We are a plumbing & HVAC construction company, operating on the West Coast of Canada and USA. Logo attached.
Industry/Entity Type
Construction - Plumbing & HVAC
Contact Information for Business Card
Name, address, phone numbers, email, website address
Look and feel
Each slider illustrates characteristics of the customer's brand and the style your logo design should communicate.

```html
<!DOCTYPE html>
<html lang="en">
<head>
<meta charset="utf-8">
<title>Cedar Ridge Mechanical — Business Card</title>
<link rel="stylesheet" href="https://fonts.googleapis.com/css2?family=Montserrat:wght@400;700&display=swap">
<style>
  :root {
    --stage: #6f6f6f;
    --stage-dark: #4a4a4a;
    --card: #141414;
    --card-edge: #2a2a2a;
    --silver: #d2d2d2;
    --silver-soft: #a9a9a9;
    --rule: #6a6a6a;
  }
  * { margin: 0; padding: 0; box-sizing: border-box; }
  html, body { width: 1200px; height: 800px; overflow: hidden; }
  body {
    background: radial-gradient(ellipse at 50% 40%, var(--stage) 0%, var(--stage-dark) 100%);
    font-family: "Montserrat", sans-serif;
    display: flex;
    align-items: center;
    justify-content: center;
    gap: 40px;
  }
  .card {
    position: relative;
    width: 540px;
    height: 310px;
    border-radius: 22px;
    background: var(--card);
    border: 1px solid var(--card-edge);
    box-shadow: 0 18px 40px rgba(0,0,0,.45);
    overflow: hidden;
    color: var(--silver);
  }
  /* Front */
  .brand {
    position: absolute;
    top: 42px;
    right: 36px;
    display: flex;
    align-items: center;
    gap: 10px;
    font-size: 17px;
    font-weight: 700;
    letter-spacing: .06em;
    text-transform: uppercase;
    color: var(--silver);
  }
  .brand-mark {
    width: 14px;
    height: 14px;
    background: var(--silver);
  }
  .divider {
    position: absolute;
    left: 34px;
    right: 36px;
    top: 172px;
    height: 1px;
    background: var(--rule);
  }
  .person {
    position: absolute;
    left: 34px;
    top: 112px;
  }
  .person-name {
    font-size: 19px;
    font-weight: 700;
    letter-spacing: .03em;
    color: var(--silver);
  }
  .person-title {
    font-size: 13px;
    color: var(--silver-soft);
    margin-top: 2px;
  }
  .contacts {
    position: absolute;
    left: 34px;
    top: 190px;
    list-style: none;
    font-size: 12.5px;
    line-height: 21px;
    color: var(--silver);
  }
  .contacts li { display: flex; align-items: center; gap: 9px; }
  .contacts svg { width: 11px; height: 11px; fill: var(--silver-soft); flex: none; }
  .address {
    position: absolute;
    right: 36px;
    top: 190px;
    text-align: right;
    font-size: 13px;
    line-height: 21px;
    color: var(--silver-soft);
  }
  /* Back */
  .pattern {
    position: absolute;
    inset: 0;
    background: linear-gradient(120deg, #0d0d0d 0%, #1b1b1b 55%, #2c2c2c 100%);
  }
  .back .brand {
    top: 50%;
    right: auto;
    left: 50%;
    transform: translate(-50%, -50%);
    font-size: 20px;
  }
</style>
</head>
<body>

  <section class="card front" aria-label="Card front">
    <div class="brand"><span class="brand-mark"></span>Cedar Ridge Mechanical</div>

    <div class="person">
      <p class="person-name">MARCUS DELANE</p>
      <p class="person-title">President</p>
    </div>

    <div class="divider"></div>

    <ul class="contacts">
      <li><svg viewBox="0 0 24 24" aria-hidden="true"><path d="M6.6 10.8a15 15 0 0 0 6.6 6.6l2.2-2.2a1 1 0 0 1 1-.25 11.4 11.4 0 0 0 3.6.57 1 1 0 0 1 1 1V20a1 1 0 0 1-1 1A17 17 0 0 1 3 4a1 1 0 0 1 1-1h3.5a1 1 0 0 1 1 1c0 1.25.2 2.45.57 3.57a1 1 0 0 1-.25 1z"/></svg>1-866-555-0142 Toll Free</li>
      <li><svg viewBox="0 0 24 24" aria-hidden="true"><path d="M6.6 10.8a15 15 0 0 0 6.6 6.6l2.2-2.2a1 1 0 0 1 1-.25 11.4 11.4 0 0 0 3.6.57 1 1 0 0 1 1 1V20a1 1 0 0 1-1 1A17 17 0 0 1 3 4a1 1 0 0 1 1-1h3.5a1 1 0 0 1 1 1c0 1.25.2 2.45.57 3.57a1 1 0 0 1-.25 1z"/></svg>213-555-0178</li>
      <li><svg viewBox="0 0 24 24" aria-hidden="true"><path d="M2 5h20v14H2zm2 2v.5l8 5 8-5V7l-8 5z"/></svg>info@cedarridgemech.com</li>
      <li><svg viewBox="0 0 24 24" aria-hidden="true"><circle cx="12" cy="12" r="10"/></svg>www.cedarridgemech.com</li>
    </ul>

    <p class="address">4120 Harbor Lane<br>Suite 200, Westbrook, CA 90000</p>
  </section>

  <section class="card back" aria-label="Card back">
    <div class="pattern" role="img" aria-label="Repeating tone-on-tone brand pattern in glossy black and grey"></div>
    <div class="brand"><span class="brand-mark"></span>Cedar Ridge Mechanical</div>
  </section>

</body>
</html>
```